Modern Business Card For A Digital Advertising Company

I'll be print on the Pell Prints Velour paper http://us.pellprints.com/products/velour/business-cards.html
Need's to be modern and use the color palette of the logo or gray scales. I think integrating the pixelation of the logo in to the card and having it wrap from one side to the other could be interesting. My company provides ad operations, web development, and number of other services to websites around the world. You can see my website at http://www.zantorhq.com
Contact info on the card needs to have
Owen Lasko
President
p.318.204.6637
owen@zantorhq.com
http://www.zantorhq.com
Doesn't necessarily need to be in that order
Website owners
Business

```html
<!DOCTYPE html>
<html lang="en">
<head>
<meta charset="utf-8">
<title>Zantor HQ — Business Card</title>
<link rel="stylesheet" href="https://fonts.googleapis.com/css2?family=Source+Sans+3:ital,wght@0,400;0,600;0,700;1,400&display=swap">
<style>
  :root {
    --backdrop: #e4e2e2;
    --ink: #0b0b0b;
    --paper: #ffffff;
    --green: #8cc63f;
    --green-deep: #5c9a2c;
    --green-light: #c3df6a;
    --cream: #f6f3c2;
  }
  * { margin: 0; padding: 0; box-sizing: border-box; }
  html, body {
    width: 1200px; height: 911px; overflow: hidden;
    background: var(--backdrop);
    font-family: "Source Sans 3", "Myriad Pro", Arial, sans-serif;
  }
  .card {
    position: absolute; left: 40px; top: 133px;
    width: 1120px; height: 645px; overflow: hidden;
    background: var(--paper);
  }
  .card-art { position: absolute; inset: 0; width: 100%; height: 100%; }
  .contact { position: absolute; color: var(--ink); white-space: nowrap; }
  .contact-name { left: 14px; top: 128px; font-size: 58px; font-weight: 700; letter-spacing: -1px; line-height: 1; }
  .contact-title { left: 112px; top: 194px; font-size: 29px; font-style: italic; line-height: 1; }
  .contact-phone { left: 24px; top: 256px; font-size: 43px; font-weight: 600; line-height: 1; }
  .contact-email { left: 24px; top: 332px; font-size: 24px; font-weight: 600; line-height: 1; }
  .contact-web { left: 22px; top: 410px; font-size: 38px; line-height: 1; }
  .brand {
    position: absolute; left: 580px; top: 300px;
    display: flex; align-items: center; gap: 14px;
  }
  .brand-square { width: 30px; height: 30px; background: var(--green); }
  .brand-name {
    font-size: 50px; font-weight: 700; color: var(--green);
    letter-spacing: 2px; line-height: 1;
  }
</style>
</head>
<body>
<main class="card">
  <svg class="card-art" viewBox="0 0 1120 645" aria-hidden="true">
    <defs>
      <linearGradient id="greenPanel" x1="0" y1="0" x2="1" y2="1">
        <stop offset="0" stop-color="var(--green-light)"/>
        <stop offset="0.45" stop-color="var(--green)"/>
        <stop offset="1" stop-color="var(--green-deep)"/>
      </linearGradient>
      <linearGradient id="creamStrip" x1="0" y1="0" x2="1" y2="0">
        <stop offset="0" stop-color="var(--green-light)"/>
        <stop offset="1" stop-color="var(--cream)"/>
      </linearGradient>
      <linearGradient id="cornerBand" x1="0" y1="0" x2="1" y2="1">
        <stop offset="0" stop-color="var(--green-deep)"/>
        <stop offset="1" stop-color="var(--green-light)"/>
      </linearGradient>
    </defs>
    <!-- black frame -->
    <rect class="frame" x="0" y="0" width="1120" height="645" fill="var(--ink)"/>
    <!-- top-right accent band -->
    <path class="corner-band" d="M900 0 H1120 V300 C1100 150 1020 40 900 0 Z" fill="url(#cornerBand)"/>
    <!-- green panel -->
    <path class="green-panel" d="M355 38 H880 C1000 38 1080 120 1080 250 V614 H355 Z" fill="url(#greenPanel)"/>
    <!-- inner curved stripe -->
    <path class="panel-stripe" d="M375 70 H860 C970 70 1045 140 1050 250" fill="none" stroke="var(--green-deep)" stroke-width="10" opacity="0.55"/>
    <!-- white contact panel -->
    <path class="contact-panel" d="M0 94 Q0 38 56 38 H355 V478 H0 Z" fill="var(--paper)"/>
    <!-- white brand panel -->
    <path class="brand-panel" d="M497 170 H860 Q943 170 943 253 V479 H497 Z" fill="var(--paper)"/>
    <!-- bottom-left diagonal bands -->
    <path class="diagonal-band" d="M0 478 H200 L340 614 V645 H0 Z" fill="url(#greenPanel)"/>
    <path class="diagonal-band" d="M0 530 H120 L235 645 H0 Z" fill="var(--green-deep)" opacity="0.6"/>
    <!-- cream base strip -->
    <path class="base-strip" d="M142 614 H1080 L1120 645 H142 Z" fill="url(#creamStrip)"/>
    <!-- pixel field -->
    <rect class="pixel-field" x="369" y="479" width="568" height="135" fill="url(#creamStrip)" opacity="0.75" role="img" aria-label="Field of scattered pale pixel squares fading across the green panel"/>
    <!-- icons -->
    <g class="icon icon-phone">
      <circle cx="393" cy="274" r="25" fill="var(--ink)"/>
      <rect x="382" y="259" width="22" height="31" rx="4" fill="none" stroke="var(--green)" stroke-width="3"/>
      <line x1="389" y1="285" x2="397" y2="285" stroke="var(--green)" stroke-width="2"/>
    </g>
    <g class="icon icon-email">
      <circle cx="393" cy="340" r="25" fill="var(--ink)"/>
      <text x="393" y="352" text-anchor="middle" font-family="Source Sans 3, sans-serif" font-weight="700" font-size="34" fill="var(--green)">@</text>
    </g>
  </svg>

  <h1 class="contact contact-name">Owen Lasko</h1>
  <p class="contact contact-title">President</p>
  <p class="contact contact-phone">318.204.6637</p>
  <p class="contact contact-email">owen@zantorhq.com</p>
  <p class="contact contact-web">www.zantorhq.com</p>

  <div class="brand">
    <span class="brand-square"></span>
    <span class="brand-name">ZANTOR HQ</span>
  </div>
</main>
</body>
</html>
```